Business Card for brovaLINK

Create a Business Card with an existing logo for brovaLINK AG. We are a Information Technology company that does consulting and developing SW to automate business processes. The main colors are given from the logo.

Industry/Entity Type

Business

Requirements
Nice to have
• we use a a font style Century Gothic in our documents

```html
<!DOCTYPE html>
<html lang="en">
<head>
<meta charset="utf-8">
<title>brovaLINK Business Card</title>
<link href="https://fonts.googleapis.com/css2?family=Questrial&display=swap" rel="stylesheet">
<style>
  :root {
    --ink: #1c1c1c;
    --paper: #ffffff;
    --lime: #7cc520;
    --lime-light: #a6dc3c;
    --stage: #e9e7e3;
    --brand-text: #2a2a2a;
    --muted: #e6e6e6;
  }
  * { margin: 0; padding: 0; box-sizing: border-box; }
  html, body { width: 1200px; height: 970px; overflow: hidden; }
  body {
    background: var(--stage);
    font-family: "Questrial", "Century Gothic", sans-serif;
    display: flex; flex-direction: column; align-items: center; justify-content: center; gap: 44px;
  }
  .card {
    position: relative; width: 760px; height: 434px; overflow: hidden;
    background: var(--paper);
    box-shadow: 0 10px 30px rgba(0,0,0,.25);
  }
  .card-shapes { position: absolute; inset: 0; width: 100%; height: 100%; }
  .brand-name {
    position: absolute; font-size: 46px; color: var(--brand-text);
    letter-spacing: 4px; line-height: 1; white-space: nowrap;
  }
  .back .brand-name { left: 52px; top: 232px; }
  .back .website {
    position: absolute; right: 70px; top: 110px; color: var(--paper);
    font-size: 20px; letter-spacing: 3px; white-space: nowrap;
  }
  .front .brand-name { left: 50px; top: 116px; }
  .name-bar {
    position: absolute; left: 34px; top: 226px; color: var(--paper);
    font-size: 19px; letter-spacing: 2px; white-space: nowrap;
  }
  .name-bar .divider { margin: 0 8px; }
  .contacts {
    position: absolute; left: 34px; top: 282px; list-style: none;
    display: grid; grid-template-columns: 250px 280px; row-gap: 16px; column-gap: 20px;
    color: var(--muted); font-size: 15px; letter-spacing: 1px;
  }
  .contacts li { display: flex; align-items: center; gap: 10px; white-space: nowrap; }
  .contacts li.wide { grid-column: 1 / 3; }
  .icon { width: 22px; height: 22px; flex: none; }
</style>
</head>
<body>

  <section class="card back" aria-label="Card back">
    <svg class="card-shapes" viewBox="0 0 760 434" aria-hidden="true">
      <rect width="760" height="434" fill="var(--ink)"/>
      <path d="M0 150 H760 V360 H0 Z" fill="var(--paper)"/>
      <path d="M310 150 C360 150 380 96 430 96 H760 V150 Z" fill="var(--lime)"/>
      <path d="M0 146 H310 C360 146 380 92 430 92 H760 V96 H430 C380 96 360 150 310 150 H0 Z" fill="var(--lime-light)"/>
      <rect y="360" width="760" height="5" fill="var(--lime)"/>
    </svg>
    <span class="website">www.brovalink.ch</span>
    <p class="brand-name">BROVALINK</p>
  </section>

  <section class="card front" aria-label="Card front">
    <svg class="card-shapes" viewBox="0 0 760 434" aria-hidden="true">
      <path d="M0 214 H380 C440 214 470 120 540 64 C560 50 580 46 610 46 H760 V434 H0 Z" fill="var(--ink)"/>
      <path d="M0 214 H380 C440 214 470 120 540 64 C560 50 580 46 610 46 H760 V52 H610 C582 52 564 56 546 70 C476 126 446 220 380 220 H0 Z" fill="var(--lime)"/>
      <path d="M0 220 H360 C380 220 392 230 400 262 H0 Z" fill="var(--lime)"/>
      <path d="M640 120 C660 96 680 92 700 92 H760 V130 H640 Z" fill="var(--lime)"/>
    </svg>
    <p class="brand-name">BROVALINK</p>
    <p class="name-bar">LENA MARQUARDT<span class="divider">|</span>GENERAL MANAGER</p>
    <ul class="contacts">
      <li>
        <svg class="icon" viewBox="0 0 22 22" aria-hidden="true"><circle cx="11" cy="11" r="10" fill="none" stroke="currentColor" stroke-width="1.4"/><path d="M7.5 6.5 L9.5 6 L10.5 8.5 L9.3 9.5 C9.9 11 11 12.1 12.5 12.7 L13.5 11.5 L16 12.5 L15.5 14.5 C11 14.8 7.2 11 7.5 6.5 Z" fill="currentColor"/></svg>
        044 210 7731
      </li>
      <li>
        <svg class="icon" viewBox="0 0 22 22" aria-hidden="true"><circle cx="11" cy="11" r="10" fill="none" stroke="currentColor" stroke-width="1.4"/><rect x="6" y="7.5" width="10" height="7" fill="none" stroke="currentColor" stroke-width="1.3"/><path d="M6 7.5 L11 11.5 L16 7.5" fill="none" stroke="currentColor" stroke-width="1.3"/></svg>
        lena@brovalink.ch
      </li>
      <li>
        <svg class="icon" viewBox="0 0 22 22" aria-hidden="true"><circle cx="11" cy="11" r="10" fill="none" stroke="currentColor" stroke-width="1.4"/><rect x="8" y="5.5" width="6" height="11" rx="1" fill="none" stroke="currentColor" stroke-width="1.3"/><circle cx="11" cy="14.3" r=".8" fill="currentColor"/></svg>
        079 318 4420
      </li>
      <li>
        <svg class="icon" viewBox="0 0 22 22" aria-hidden="true"><circle cx="11" cy="11" r="10" fill="none" stroke="currentColor" stroke-width="1.4"/><circle cx="11" cy="11" r="5.5" fill="none" stroke="currentColor" stroke-width="1.2"/><path d="M5.5 11 H16.5 M11 5.5 C8.5 8 8.5 14 11 16.5 M11 5.5 C13.5 8 13.5 14 11 16.5" fill="none" stroke="currentColor" stroke-width="1.1"/></svg>
        www.brovalink.ch
      </li>
      <li class="wide">
        <svg class="icon" viewBox="0 0 22 22" aria-hidden="true"><circle cx="11" cy="11" r="10" fill="none" stroke="currentColor" stroke-width="1.4"/><path d="M11 17 C8 13 7 11.5 7 9.5 A4 4 0 0 1 15 9.5 C15 11.5 14 13 11 17 Z" fill="currentColor"/><circle cx="11" cy="9.5" r="1.5" fill="var(--ink)"/></svg>
        42 Lindenhof Road, 8001 Zurich
      </li>
    </ul>
  </section>

</body>
</html>
```